20 year old business card needs re-design

We need to redesign our corporate business card look. We need something that appears more modern, eye catchy but professional.

Target Market(s)

manufacturing industry

Industry/Entity Type

Manufacturer

Contact Information for Business Card

One side can have the logo. Other side can have contact information.

Font styles to use
Serif

Colors
3277b5
33b8a4
ffffff

Requirements
Must have
• Eye catchy - need to standout from the crowd. company logo cannot change. Full name, job title, phone number and email address.
Should not have
• Fax, business address is not necessary.

```html
<!DOCTYPE html>
<html lang="en">
<head>
<meta charset="utf-8">
<title>Norvale Industrial – Business Card</title>
<link rel="stylesheet" href="https://fonts.googleapis.com/css2?family=Archivo:wght@400;700;800&display=swap">
<style>
  :root {
    --backdrop: #2b2b2d;
    --card-blue: #1f47a6;
    --card-blue-light: #2a58c2;
    --card-white: #f4f4f4;
    --crescent: #1b1b1d;
    --ink-dark: #1c1c1e;
    --ink-light: #ffffff;
    --icon-bg: #e8e8ea;
  }
  * { margin: 0; padding: 0; box-sizing: border-box; }
  html, body {
    width: 1200px; height: 997px; overflow: hidden;
    background: var(--backdrop);
    font-family: "Archivo", Arial, sans-serif;
  }
  .stage {
    width: 1200px; height: 997px;
    display: flex; flex-direction: column;
    align-items: center; justify-content: center; gap: 56px;
  }
  .card {
    position: relative;
    width: 700px; height: 400px;
    border-radius: 14px; overflow: hidden;
    box-shadow: 0 18px 40px rgba(0,0,0,.5);
  }
  /* Back side */
  .card-back {
    background: linear-gradient(135deg, var(--card-blue-light), var(--card-blue));
    display: flex; align-items: center; justify-content: center;
  }
  .brand-name {
    font-weight: 800; letter-spacing: -1px; line-height: 1;
    display: flex; align-items: center; gap: 16px;
  }
  .card-back .brand-name { color: var(--ink-light); font-size: 64px; }
  .brand-mark { width: 20px; height: 20px; background: currentColor; flex: none; }

  /* Front side */
  .card-front { background: var(--card-blue); }
  .card-front .shapes { position: absolute; inset: 0; }
  .card-front .brand-name {
    position: absolute; left: 46px; top: 148px;
    color: var(--ink-dark); font-size: 46px;
    align-items: flex-start; gap: 14px;
  }
  .card-front .brand-words { display: flex; flex-direction: column; gap: 4px; }
  .card-front .brand-mark { width: 14px; height: 14px; margin-top: 16px; }
  .person {
    position: absolute; right: 36px; top: 34px;
    text-align: right; color: var(--ink-light);
  }
  .person-name { font-weight: 700; font-size: 19px; letter-spacing: .5px; }
  .person-title { font-weight: 700; font-size: 11px; letter-spacing: .6px; margin-top: 4px; }
  .contact {
    position: absolute; right: 36px; top: 170px;
    list-style: none; color: var(--ink-light);
    text-align: right; font-size: 16px; line-height: 1.25;
  }
  .contact li { display: flex; justify-content: flex-end; align-items: center; gap: 12px; margin-bottom: 14px; }
  .contact .address { margin-bottom: 22px; }
  .icon {
    width: 20px; height: 20px; flex: none;
    background: var(--icon-bg); border-radius: 4px;
    display: flex; align-items: center; justify-content: center;
  }
  .icon svg { width: 12px; height: 12px; }
  .icon-spacer { width: 20px; flex: none; }
</style>
</head>
<body>
<main class="stage">
  <section class="card card-back" aria-label="Card back">
    <div class="brand-name"><span class="brand-mark"></span>Norvale Industrial</div>
  </section>

  <section class="card card-front" aria-label="Card front">
    <svg class="shapes" viewBox="0 0 700 400" preserveAspectRatio="none" aria-hidden="true">
      <path d="M0 0 H350 C470 90 495 260 452 400 H0 Z" fill="var(--crescent)"/>
      <path d="M0 0 H330 C430 90 450 260 410 400 H0 Z" fill="var(--card-white)"/>
    </svg>

    <div class="brand-name">
      <span class="brand-mark"></span>
      <span class="brand-words"><span>Norvale</span><span>Industrial</span></span>
    </div>

    <div class="person">
      <div class="person-name">DANA WHITFIELD</div>
      <div class="person-title">FOUNDER &amp; CEO</div>
    </div>

    <ul class="contact">
      <li class="address"><span>P.O. Box 5520<br>Lakeport, MI 48059</span><span class="icon-spacer"></span></li>
      <li><span>555-014-2270</span>
        <span class="icon"><svg viewBox="0 0 12 12"><rect x="3" y="1" width="6" height="10" rx="1" fill="none" stroke="#333" stroke-width="1.3"/></svg></span></li>
      <li><span>norvaleind.com</span>
        <span class="icon"><svg viewBox="0 0 12 12"><rect x="1" y="3" width="10" height="6" fill="none" stroke="#333" stroke-width="1.2"/><path d="M1 3 L6 7 L11 3" fill="none" stroke="#333" stroke-width="1.2"/></svg></span></li>
      <li><span>dw@norvaleind.com</span>
        <span class="icon"><svg viewBox="0 0 12 12"><path d="M2 10 L10 2 M4 3 H9 V8" fill="none" stroke="#333" stroke-width="1.4"/></svg></span></li>
      <li><span>www.norvaleind.com</span><span class="icon-spacer"></span></li>
    </ul>
  </section>
</main>
</body>
</html>
```